Corvane Capital Business Cards

These are professional business cards that are for my family office.
Put fake emails and phone numbers as of now until I finalize those components. This family office controls my families investments, assets, and future. The cards should be professional.
..
.
.
.
I just uploaded another variation of a logo I would like to see as a business card to I am inbeteen which logo to use

Target Market(s)

business

Industry/Entity Type

business

Contact Information for Business Card

Professional, wealth related, finance related.

Requirements
Must have
• Logo

```html
<!DOCTYPE html>
<html lang="en">
<head>
<meta charset="utf-8">
<title>Corvane Capital Business Cards</title>
<link href="https://fonts.googleapis.com/css2?family=Cinzel:wght@400;600;700&display=swap" rel="stylesheet">
<style>
  :root {
    --ink: #1b1f2e;
    --paper: #ffffff;
    --backdrop: #3b3b3d;
    --muted-grey: #a8a8a8;
  }
  * { margin: 0; padding: 0; box-sizing: border-box; }
  html, body {
    width: 1200px; height: 1059px; overflow: hidden;
    background: var(--backdrop);
  }
  .canvas { position: relative; width: 1200px; height: 1059px; }
  .card {
    position: absolute;
    background: var(--paper);
    border-radius: 22px;
    overflow: hidden;
    color: var(--ink);
    font-family: "Cinzel", serif;
  }
  .card-front { left: 256px; top: 100px; width: 688px; height: 393px; }
  .card-back  { left: 253px; top: 536px; width: 694px; height: 396px; }

  .contact-column {
    position: absolute; left: 20px; top: 0; width: 312px;
    text-align: center;
  }
  .firm-name-small { position: absolute; left: 0; right: 0; top: 34px; font-size: 25px; font-weight: 700; letter-spacing: 0.5px; white-space: nowrap; }
  .person-name { position: absolute; left: 0; right: 0; top: 90px; font-size: 33px; font-weight: 600; letter-spacing: 1px; }
  .person-title { position: absolute; left: 0; right: 0; top: 135px; font-size: 16px; letter-spacing: 1px; }
  .icon-row {
    position: absolute; left: 0; right: 0; top: 176px;
    display: flex; align-items: center; justify-content: center; gap: 4px;
  }
  .icon-row .rule { width: 63px; height: 2px; background: var(--ink); margin: 0 8px; }
  .icon-box {
    width: 27px; height: 27px; border-radius: 6px; background: var(--ink);
    display: flex; align-items: center; justify-content: center;
  }
  .contact-line { position: absolute; left: 0; right: 0; font-size: 16px; letter-spacing: 0.5px; white-space: nowrap; }
  .contact-phone { top: 219px; font-size: 18px; }
  .contact-email { top: 247px; }
  .contact-web { top: 275px; }
  .divider { position: absolute; left: 72px; width: 206px; top: 307px; height: 2px; background: var(--ink); }
  .address { position: absolute; left: 0; right: 0; top: 321px; font-size: 17px; line-height: 28px; letter-spacing: 0.5px; }

  .mark-circle { position: absolute; }
  .front-circle { left: 422px; top: 25px; width: 264px; height: 264px; }
  .firm-name-large {
    position: absolute; left: 334px; right: 12px; top: 322px;
    text-align: center; white-space: nowrap;
    font-size: 35px; font-weight: 700; letter-spacing: 0.5px;
  }

  .back-circle { left: 242px; top: 62px; width: 212px; height: 212px; }
  .firm-name-back {
    position: absolute; left: 0; right: 0; top: 294px; text-align: center;
    font-size: 40px; font-weight: 700; letter-spacing: 1px;
  }
</style>
</head>
<body>
<div class="canvas">
  <section class="card card-front">
    <div class="contact-column">
      <div class="firm-name-small">Corvane Capital</div>
      <div class="person-name">DANIEL HALE</div>
      <div class="person-title">Managing Director</div>
      <div class="icon-row">
        <span class="rule"></span>
        <span class="icon-box">
          <svg width="17" height="17" viewBox="0 0 24 24" aria-label="phone"><path fill="#fff" d="M6.6 10.8a15 15 0 0 0 6.6 6.6l2.2-2.2a1 1 0 0 1 1-.25 11.4 11.4 0 0 0 3.6.57 1 1 0 0 1 1 1V20a1 1 0 0 1-1 1A17 17 0 0 1 3 4a1 1 0 0 1 1-1h3.5a1 1 0 0 1 1 1c0 1.25.2 2.45.57 3.57a1 1 0 0 1-.25 1z"/></svg>
        </span>
        <span class="icon-box">
          <svg width="17" height="17" viewBox="0 0 24 24" aria-label="email"><rect x="2" y="5" width="20" height="14" rx="2" fill="#fff"/><path d="M3 6l9 7 9-7" fill="none" stroke="#1b1f2e" stroke-width="2"/></svg>
        </span>
        <span class="icon-box">
          <svg width="17" height="17" viewBox="0 0 24 24" aria-label="website"><circle cx="12" cy="12" r="9" fill="none" stroke="#fff" stroke-width="2"/><path d="M3 12h18M12 3c3 3 3 15 0 18M12 3c-3 3-3 15 0 18" fill="none" stroke="#fff" stroke-width="1.5"/></svg>
        </span>
        <span class="rule"></span>
      </div>
      <div class="contact-line contact-phone">123 456 789</div>
      <div class="contact-line contact-email">INFO@CORVANEMAIL.COM</div>
      <div class="contact-line contact-web">WWW.CORVANECAPITAL.COM</div>
      <div class="divider"></div>
      <div class="address">Your address, City<br>State, Zip 1234</div>
    </div>
    <svg class="mark-circle front-circle" viewBox="0 0 264 264"><circle cx="132" cy="132" r="128" fill="none" stroke="var(--ink)" stroke-width="5"/></svg>
    <div class="firm-name-large">Corvane Capital</div>
  </section>

  <section class="card card-back">
    <svg class="mark-circle back-circle" viewBox="0 0 212 212"><circle cx="106" cy="106" r="102" fill="none" stroke="var(--ink)" stroke-width="5"/></svg>
    <div class="firm-name-back">Corvane Capital</div>
  </section>
</div>
</body>
</html>
```